Dew Petal Ritual. Home based organic skin care manufacturer

We need top notch user friendly and interactive web6/mobile site that will cater to online e commerce, retail of our varieties of products and real time communication with online buyers.

Coding

Coded - Design and coding required

Number of Pages Required

1 page

```html
<!DOCTYPE html>
<html lang="en">
<head>
<meta charset="utf-8">
<title>Dew Petal Ritual — Home Based Organic Skin Care</title>
<link href="https://fonts.googleapis.com/css2?family=Playfair+Display:wght@400;700;900&family=Montserrat:wght@400;600&family=Arimo:wght@400&display=swap" rel="stylesheet">
<style>
  :root {
    --green: #8cb52d;
    --green-bright: #7db600;
    --olive: #7d9a44;
    --ink: #111111;
    --text: #2b2b2b;
    --white: #ffffff;
    --black: #000000;
    --card-line: #e6e6e6;
    --arrow-grey: #e4e4e4;
  }
  * { box-sizing: border-box; margin: 0; padding: 0; }
  html, body { width: 1200px; height: 2826px; overflow: hidden; background: var(--white); }
  body { position: relative; font-family: "Playfair Display", serif; color: var(--text); }
  .abs { position: absolute; }

  /* Hero */
  .hero { position: absolute; left: 0; top: 0; width: 1200px; height: 574px; overflow: hidden; }
  .hero-photo { position: absolute; inset: 0; }
  .brand { position: absolute; left: 98px; top: 52px; font-family: "Playfair Display", serif; font-weight: 700; font-size: 26px; color: var(--white); letter-spacing: 0.5px; }
  .brand::before { content: ""; display: inline-block; width: 12px; height: 12px; border-radius: 50%; background: var(--white); margin-right: 10px; vertical-align: middle; }
  .nav { position: absolute; top: 26px; font-weight: 700; font-size: 18px; color: var(--white); }
  .nav-bar { position: absolute; left: 451px; top: 29px; width: 3px; height: 18px; background: var(--white); }
  .nav-icon { position: absolute; top: 26px; }
  .hero-title { position: absolute; left: 98px; color: var(--white); font-weight: 900; line-height: 1; }
  .hero-title.small { top: 176px; font-size: 64px; }
  .hero-title.large { top: 250px; font-size: 88px; }
  .hero-sub { position: absolute; left: 107px; top: 358px; color: var(--white); font-weight: 700; font-size: 19px; line-height: 28px; text-transform: uppercase; }

  /* Categories */
  .category { position: absolute; top: 616px; height: 432px; border-radius: 130px 0 110px 0; overflow: hidden; }
  .category-label { position: absolute; left: 0; right: 0; color: var(--white); font-weight: 700; font-size: 26px; text-align: center; line-height: 37px; }

  /* Sections */
  .section-title { position: absolute; font-weight: 900; font-size: 33px; color: var(--ink); text-transform: uppercase; line-height: 1.1; }
  .section-copy { position: absolute; font-size: 17px; line-height: 25px; color: var(--text); }
  .arrow { position: absolute; width: 42px; height: 42px; border-radius: 50%; display: flex; align-items: center; justify-content: center; }
  .arrow.on { background: var(--green-bright); }
  .arrow.off { background: var(--arrow-grey); }

  .product { position: absolute; width: 228px; background: var(--white); border: 1px solid var(--card-line); border-radius: 3px; }
  .product.raised { border: none; box-shadow: 0 4px 14px rgba(0,0,0,0.16); }
  .product-img { position: absolute; left: 34px; right: 34px; top: 16px; height: 174px; }
  .product-name { position: absolute; left: 0; right: 0; top: 204px; text-align: center; font-weight: 700; font-size: 19px; line-height: 26px; color: var(--ink); }
  .add-cart { position: absolute; left: 45px; width: 140px; height: 37px; background: var(--green-bright); color: var(--white); border-radius: 4px; font-weight: 700; font-size: 16px; display: flex; align-items: center; justify-content: center; }

  /* Band */
  .band { position: absolute; left: 0; top: 1526px; width: 1200px; height: 365px; }
  .band-title { position: absolute; left: 0; right: 0; top: 1626px; text-align: center; color: var(--white); font-weight: 900; font-size: 40px; }
  .band-btn { position: absolute; left: 527px; top: 1702px; width: 147px; height: 46px; border: 2px solid var(--white); border-radius: 6px; color: var(--white); font-weight: 700; font-size: 22px; display: flex; align-items: center; justify-content: center; }

  /* Features */
  .features { position: absolute; left: 86px; top: 2361px; width: 1029px; height: 67px; background: var(--olive); display: flex; align-items: center; justify-content: center; gap: 18px; font-family: "Montserrat", sans-serif; font-weight: 600; font-size: 11.5px; color: var(--white); letter-spacing: 0.3px; }
  .feature { display: flex; align-items: center; gap: 12px; }
  .feature-rule { width: 44px; height: 1px; background: var(--white); }

  /* Footer */
  .footer { position: absolute; left: 0; top: 2413px; width: 1200px; height: 413px; background: var(--black); }
  .footer-brand { position: absolute; left: 84px; top: 2560px; font-weight: 700; font-size: 30px; color: var(--white); }
  .social { position: absolute; top: 2665px; width: 31px; height: 31px; border: 1.5px solid var(--white); border-radius: 50%; }
  .footer-head { position: absolute; top: 2478px; font-size: 22px; color: var(--white); }
  .footer-head::after { content: ""; position: absolute; left: 2px; top: 42px; width: 32px; height: 3px; background: var(--white); }
  .footer-text { position: absolute; font-family: "Arimo", sans-serif; font-size: 14.5px; line-height: 23px; color: var(--white); }
  .footer-label { position: absolute; font-family: "Arimo", sans-serif; font-size: 14px; color: #d8d8d8; }
  .email-field { position: absolute; left: 810px; top: 2605px; width: 276px; height: 40px; background: var(--white); border-radius: 20px; font-family: "Arimo", sans-serif; font-size: 12.5px; color: #222; padding-left: 20px; display: flex; align-items: center; }
  .footer-rule { position: absolute; left: 112px; top: 2743px; width: 976px; height: 1px; background: #9a9a9a; }
  .copyright { position: absolute; left: 0; right: 0; top: 2780px; text-align: center; font-family: "Montserrat", sans-serif; font-size: 15px; color: var(--white); }
</style>
</head>
<body>

<header class="hero">
  <svg class="hero-photo" width="1200" height="574" viewBox="0 0 1200 574" role="img" aria-label="Woman relaxing with a clay face mask surrounded by tropical leaves and flowers">
    <defs>
      <linearGradient id="heroRight" x1="0" y1="0" x2="1" y2="1">
        <stop offset="0" stop-color="#c9b2a4"/>
        <stop offset="0.5" stop-color="#dcc2b2"/>
        <stop offset="1" stop-color="#b58a73"/>
      </linearGradient>
      <linearGradient id="heroLeft" x1="0" y1="0" x2="1" y2="1">
        <stop offset="0" stop-color="#3b6e75"/>
        <stop offset="0.5" stop-color="#4d6b5a"/>
        <stop offset="1" stop-color="#7a6a3a"/>
      </linearGradient>
    </defs>
    <rect width="1200" height="574" fill="url(#heroRight)"/>
    <polygon points="0,0 1200,0 0,574" fill="url(#heroLeft)"/>
    <line x1="-4" y1="576" x2="1204" y2="-2" stroke="#ffffff" stroke-width="5"/>
  </svg>

  <div class="brand">Dew Petal Ritual</div>

  <div class="nav-bar"></div>
  <div class="nav" style="left:461px;">Home</div>
  <div class="nav" style="left:552px;">Skin Care</div>
  <div class="nav" style="left:674px;">Home based organic</div>
  <div class="nav" style="left:878px;">About Us</div>
  <svg class="nav-icon" style="left:985px;" width="20" height="22" viewBox="0 0 20 22" aria-label="Search"><circle cx="8" cy="9" r="6" fill="none" stroke="#fff" stroke-width="3"/><line x1="12.5" y1="13.5" x2="18" y2="19" stroke="#fff" stroke-width="3" stroke-linecap="round"/></svg>
  <svg class="nav-icon" style="left:1035px;" width="18" height="22" viewBox="0 0 18 22" aria-label="Account"><circle cx="9" cy="6" r="5" fill="#fff"/><path d="M1 20 Q1 12 9 12 Q17 12 17 20 Z" fill="#fff"/></svg>
  <svg class="nav-icon" style="left:1079px;" width="22" height="22" viewBox="0 0 22 22" aria-label="Cart"><path d="M1 3 H5 L8 14 H18 L20 6 H6" fill="#fff" stroke="#fff" stroke-width="2" stroke-linejoin="round"/><circle cx="9" cy="18" r="2" fill="#fff"/><circle cx="17" cy="18" r="2" fill="#fff"/></svg>

  <div class="hero-title small">DEW PETAL</div>
  <div class="hero-title large">RITUAL</div>
  <div class="hero-sub">Home based organic skin<br>care manufacturer.</div>
</header>

<section class="categories">
  <div class="category" style="left:103px; width:316px;">
    <svg width="316" height="432" role="img" aria-label="Woman receiving a facial mask treatment"><defs><linearGradient id="catA" x1="0" y1="0" x2="0" y2="1"><stop offset="0" stop-color="#e9dce4"/><stop offset="0.55" stop-color="#b981b8"/><stop offset="1" stop-color="#6a1a72"/></linearGradient></defs><rect width="316" height="432" fill="url(#catA)"/></svg>
    <div class="category-label" style="top:358px;">FACIALS</div>
  </div>
  <div class="category" style="left:457px; width:317px;">
    <svg width="317" height="432" role="img" aria-label="Bearded man shown in profile"><defs><linearGradient id="catB" x1="0" y1="0" x2="0" y2="1"><stop offset="0" stop-color="#9fa8ab"/><stop offset="0.55" stop-color="#4e4f52"/><stop offset="1" stop-color="#0f0f10"/></linearGradient></defs><rect width="317" height="432" fill="url(#catB)"/></svg>
    <div class="category-label" style="top:333px;">HAIR AND BEARD<br>CARE</div>
  </div>
  <div class="category" style="left:812px; width:285px;">
    <svg width="285" height="432" role="img" aria-label="Smiling woman touching her glowing skin"><defs><linearGradient id="catC" x1="0" y1="0" x2="0" y2="1"><stop offset="0" stop-color="#a9a873"/><stop offset="0.5" stop-color="#8a6a52"/><stop offset="1" stop-color="#2a1a1c"/></linearGradient></defs><rect width="285" height="432" fill="url(#catC)"/></svg>
    <div class="category-label" style="top:333px;">TREATMENTS</div>
  </div>
</section>

<section class="skin-care">
  <h2 class="section-title" style="left:92px; top:1140px;">Our Skin Care</h2>
  <p class="section-copy" style="left:92px; top:1200px; width:265px;">Lorem ipsum dolor sit amet, consectetur adipiscing elit, sed do eiusmod tempor incididunt ut labore et dolore magna aliqua. Ut enim ad minim veniam, quis nostrud exercitation ullamco laboris nisi ut</p>
  <div class="arrow on" style="left:91px; top:1372px;"><svg width="12" height="14" viewBox="0 0 12 14"><path d="M8 2 L3 7 L8 12" fill="none" stroke="#fff" stroke-width="2.4"/></svg></div>
  <div class="arrow off" style="left:144px; top:1372px;"><svg width="12" height="14" viewBox="0 0 12 14"><path d="M4 2 L9 7 L4 12" fill="none" stroke="#555" stroke-width="2"/></svg></div>

  <div class="product" style="left:370px; top:1121px; height:280px;">
    <svg class="product-img" width="160" height="174" role="img" aria-label="Yellow glow oil bottle"><rect x="56" y="4" width="46" height="42" rx="6" fill="#e6e6e6"/><rect x="50" y="44" width="58" height="126" rx="10" fill="#f2c53d"/></svg>
    <div class="product-name">Glow Oil</div>
  </div>
  <div class="product raised" style="left:612px; top:1120px; height:304px;">
    <svg class="product-img" width="160" height="174" role="img" aria-label="White face cleansing wash bottle"><rect x="60" y="4" width="40" height="40" rx="6" fill="#e4e4e4"/><rect x="54" y="42" width="52" height="128" rx="8" fill="#f6f6f6" stroke="#e2e2e2"/></svg>
    <div class="product-name">Face Cleansing Wash</div>
    <div class="add-cart" style="top:248px;">ADD TO CART</div>
  </div>
  <div class="product" style="left:857px; top:1121px; height:280px;">
    <svg class="product-img" width="160" height="174" role="img" aria-label="Brightening body milk jar"><rect x="4" y="48" width="152" height="20" rx="3" fill="#b9b9b9"/><rect x="6" y="66" width="148" height="86" fill="#f4f4f4"/><rect x="6" y="128" width="148" height="8" fill="#2d1f4d"/></svg>
    <div class="product-name">Brightening Body<br>Milk</div>
  </div>
</section>

<section>
  <svg class="band" width="1200" height="365" role="img" aria-label="Woman splashing water on her face, tinted green"><defs><radialGradient id="bandG" cx="0.5" cy="0.55" r="0.6"><stop offset="0" stop-color="#9ab83a"/><stop offset="1" stop-color="#88b42e"/></radialGradient></defs><rect width="1200" height="365" fill="url(#bandG)"/></svg>
  <h2 class="band-title">Real-Time Communication With Online Buyers.</h2>
  <div class="band-btn">Contact Us</div>
</section>

<section class="new-products">
  <div class="product raised" style="left:92px; top:1975px; height:302px;">
    <svg class="product-img" width="160" height="174" role="img" aria-label="Balancing facial toner jar"><rect x="8" y="20" width="144" height="46" rx="4" fill="#a89a2e"/><rect x="8" y="64" width="144" height="86" fill="#f4f4f4"/></svg>
    <div class="product-name">Balancing Facial Toner</div>
    <div class="add-cart" style="top:246px;">ADD TO CART</div>
  </div>
  <div class="product" style="left:336px; top:1975px; height:277px;">
    <svg class="product-img" width="160" height="174" role="img" aria-label="Age reverse serum jar"><rect x="4" y="20" width="152" height="46" rx="4" fill="#a89a2e"/><rect x="4" y="64" width="152" height="86" fill="#f4f4f4"/></svg>
    <div class="product-name">Age Reverse Serum</div>
  </div>
  <div class="product" style="left:579px; top:1975px; height:277px;">
    <svg class="product-img" width="160" height="174" role="img" aria-label="Open jar of face and body scrub"><path d="M20 40 Q80 10 140 40 L140 66 L20 66 Z" fill="#f1f1f1"/><rect x="14" y="64" width="134" height="86" fill="#f6eedd"/><rect x="14" y="128" width="134" height="8" fill="#111"/></svg>
    <div class="product-name">Face and body scrub</div>
  </div>

  <h2 class="section-title" style="left:800px; top:1990px; width:284px; text-align:right; line-height:40px;">Our New<br>Products</h2>
  <p class="section-copy" style="left:822px; top:2080px; width:262px; text-align:right;">Lorem ipsum dolor sit amet, consectetur adipiscing elit, sed do eiusmod tempor incididunt ut labore et dolore magna aliqua.</p>
  <div class="arrow off" style="left:990px; top:2199px;"><svg width="12" height="14" viewBox="0 0 12 14"><path d="M8 2 L3 7 L8 12" fill="none" stroke="#222" stroke-width="2.2"/></svg></div>
  <div class="arrow on" style="left:1042px; top:2199px;"><svg width="12" height="14" viewBox="0 0 12 14"><path d="M4 2 L9 7 L4 12" fill="none" stroke="#fff" stroke-width="2.4"/></svg></div>
</section>

<footer>
  <div class="footer"></div>
  <div class="features">
    <div class="feature"><svg width="32" height="20" viewBox="0 0 32 20"><rect x="1" y="3" width="19" height="12" fill="none" stroke="#fff" stroke-width="1.4"/><path d="M20 7 H27 L31 11 V15 H20" fill="none" stroke="#fff" stroke-width="1.4"/><circle cx="7" cy="17" r="2.2" fill="#7d9a44" stroke="#fff" stroke-width="1.4"/><circle cx="25" cy="17" r="2.2" fill="#7d9a44" stroke="#fff" stroke-width="1.4"/></svg>FAST &amp; PROMPT DELIVERY</div>
    <div class="feature-rule"></div>
    <div class="feature"><svg width="16" height="22" viewBox="0 0 16 22"><path d="M4 10 V6 a4 4 0 0 1 8 0 V10" fill="none" stroke="#fff" stroke-width="1.4"/><rect x="1" y="10" width="14" height="11" fill="none" stroke="#fff" stroke-width="1.4"/></svg>SECURE PAYMENT</div>
    <div class="feature-rule"></div>
    <div class="feature"><svg width="18" height="18" viewBox="0 0 18 18"><rect x="1" y="1" width="16" height="16" rx="2" fill="none" stroke="#fff" stroke-width="1.4"/><path d="M5 9 L8 12 L13 6" fill="none" stroke="#fff" stroke-width="1.6"/></svg>100% GUARANTEED</div>
    <div class="feature-rule"></div>
    <div class="feature"><svg width="26" height="24" viewBox="0 0 26 24"><rect x="1" y="6" width="24" height="17" rx="2" fill="none" stroke="#fff" stroke-width="1.4"/><path d="M4 6 L18 1 L20 6" fill="none" stroke="#fff" stroke-width="1.4"/><rect x="17" y="12" width="8" height="5" fill="none" stroke="#fff" stroke-width="1.4"/></svg>MONEY BACK GUARANTEED</div>
  </div>

  <div class="footer-brand">Dew Petal Ritual</div>
  <div class="social" style="left:100px;" aria-label="Social link"></div>
  <div class="social" style="left:138px;" aria-label="Social link"></div>

  <h3 class="footer-head" style="left:363px; font-weight:400;">More Info</h3>
  <div class="footer-text" style="left:363px; top:2536px; line-height:30px;">Terms &amp; Conditions<br>Privacy Policy<br>About Us<br>Support</div>

  <h3 class="footer-head" style="left:561px; font-weight:400;">Contact Us</h3>
  <div class="footer-label" style="left:561px; top:2536px;">ADDRESS</div>
  <div class="footer-text" style="left:561px; top:2558px; width:180px;"><svg width="9" height="12" viewBox="0 0 9 12"><path d="M4.5 0 A4.5 4.5 0 0 1 9 4.5 C9 7 4.5 12 4.5 12 C4.5 12 0 7 0 4.5 A4.5 4.5 0 0 1 4.5 0 Z" fill="#fff"/><circle cx="4.5" cy="4.5" r="1.6" fill="#000"/></svg> Lorem ipsum dolor sit amet, consectеturs</div>
  <div class="footer-label" style="left:561px; top:2616px;">PHONE</div>
  <div class="footer-text" style="left:561px; top:2637px;"><svg width="12" height="12" viewBox="0 0 12 12"><path d="M2 0 L4.5 0 L5.5 3 L4 4.5 Q5.5 7 7.5 8 L9 6.5 L12 7.5 L12 10 Q11 12 9 12 Q0 9 0 2 Q0 0 2 0 Z" fill="#fff"/></svg> +1 555-014-2290</div>
  <div class="footer-label" style="left:561px; top:2676px;">EMAIL</div>
  <div class="footer-text" style="left:561px; top:2696px; font-size:16px;"><svg width="14" height="11" viewBox="0 0 14 11"><rect width="14" height="11" rx="1" fill="#fff"/><path d="M0.5 1 L7 6 L13.5 1" fill="none" stroke="#000" stroke-width="1.2"/></svg> hello@dewpetalritual.com</div>

  <h3 class="footer-head" style="left:813px; font-weight:400;">Newsletter</h3>
  <div class="footer-text" style="left:813px; top:2535px; width:270px;">Lorem ipsum dolor sit amet, consectetur adipiscing elit, sed do eiusmod tempor</div>
  <div class="email-field">Enter Email
    <svg style="position:absolute; right:16px; top:10px;" width="20" height="20" viewBox="0 0 20 20"><circle cx="10" cy="10" r="10" fill="#000"/><path d="M5 10 L15 5 L12 15 L10 11 Z" fill="#fff"/></svg>
  </div>

  <div class="footer-rule"></div>
  <div class="copyright">© copyrights 2023 Dew Petal Ritual |&nbsp; All Rights Reserved</div>
</footer>

</body>
</html>
```